Business card design for holistic health care clinic

We need a double-sided business card design for our holistic health care clinic that integrates our logo design and also its color scheme. My business is called Valmira. It is an integrative medicine clinic. You have already done the logo for me. Please ensure an elegant and upscale design that is not cluttered, but still has all the necessary information (please see below for details).

Target Market(s)

Wellness, fitness, rehabilitation for educated, well-traveled open-minded clients who are focused on natural, organic, balanced and preventive healthcare and lifestyle.

Industry/Entity Type

Medical

Contact Information for Business Card

Modern, clean.

Number of Pages Required

1 page

Font styles to use
Serif
Sans Serif

Colors

Designer to choose colors to be used in the design.

Requirements
Must have
• Logo on one side, all other information on the other side.
• Other information should include:
• Tobias Wrenfeld - DOE, CPT, LMT
• 4100 East Marrow Drive
• Austin, TX 78119
• 512 555 0148
• 818 555 0192
• info@ValmiraHealth.example
• t.wrenfeld@ValmiraHealth.example
Nice to have
• Darker background on front - but not totally black - shaded/dark gray.

```html
<!DOCTYPE html>
<html lang="en">
<head>
<meta charset="utf-8">
<title>Valmira – Business Card</title>
<link href="https://fonts.googleapis.com/css2?family=Source+Sans+3:wght@400;600;700&display=swap" rel="stylesheet">
<style>
  :root {
    --backdrop: #a9a9a9;
    --card: #1b1c1e;
    --brand-blue: #1a93d1;
    --text-light: #f4f4f4;
  }
  html, body {
    margin: 0;
    padding: 0;
    width: 1200px;
    height: 900px;
    overflow: hidden;
    background: var(--backdrop);
    font-family: "Source Sans 3", "Helvetica Neue", Arial, sans-serif;
  }
  .stage {
    position: relative;
    width: 1200px;
    height: 900px;
  }
  .card {
    position: absolute;
    top: 275px;
    width: 478px;
    height: 295px;
    background: var(--card);
    box-shadow: 2px 3px 6px rgba(0,0,0,0.35);
  }
  .card--info {
    left: 116px;
    border-radius: 0 48px 0 48px;
  }
  .card--brand {
    left: 622px;
    border-radius: 48px 0 48px 0;
  }
  .wordmark {
    position: absolute;
    margin: 0;
    color: var(--brand-blue);
    font-weight: 700;
    letter-spacing: 1px;
    line-height: 1;
  }
  .tagline {
    position: absolute;
    margin: 0;
    color: var(--brand-blue);
    font-weight: 600;
    line-height: 1;
  }
  .card--info .wordmark {
    right: 20px;
    top: 62px;
    font-size: 54px;
  }
  .card--info .tagline {
    right: 22px;
    top: 112px;
    font-size: 15px;
  }
  .card--brand .wordmark {
    left: 0;
    right: 0;
    text-align: center;
    top: 128px;
    font-size: 54px;
  }
  .card--brand .tagline {
    left: 0;
    right: 0;
    text-align: center;
    top: 177px;
    font-size: 15px;
  }
  .holder {
    position: absolute;
    left: 34px;
    top: 139px;
    margin: 0;
    color: var(--brand-blue);
    font-size: 18px;
    font-weight: 600;
    line-height: 1;
  }
  .holder__credentials {
    font-size: 12.5px;
    font-weight: 400;
  }
  .divider {
    position: absolute;
    left: 35px;
    top: 164px;
    width: 422px;
    height: 2px;
    background: var(--brand-blue);
  }
  .contact-list {
    position: absolute;
    right: 22px;
    top: 175px;
    margin: 0;
    padding: 0;
    list-style: none;
    color: var(--text-light);
    font-size: 13.5px;
    text-align: right;
  }
  .contact-list li {
    height: 20px;
    line-height: 20px;
    display: flex;
    justify-content: flex-end;
    align-items: center;
  }
  .contact-list svg {
    width: 10px;
    height: 10px;
    margin-left: 10px;
    fill: var(--brand-blue);
  }
</style>
</head>
<body>
<main class="stage">
  <section class="card card--info" aria-label="Card back: contact details">
    <p class="wordmark">VALMIRA</p>
    <p class="tagline">Integrative Holistic Medicine</p>
    <p class="holder">Tobias Wrenfeld <span class="holder__credentials">- DOE, CPT, LMT</span></p>
    <div class="divider"></div>
    <ul class="contact-list">
      <li>512 555 0148
        <svg viewBox="0 0 10 10" aria-hidden="true"><path d="M2 0.5 L3.6 2.6 L2.7 3.6 Q3.6 5.6 6.4 7.3 L7.4 6.4 L9.5 8 L8.3 9.5 Q4.5 9.3 0.6 1.7 Z"/></svg>
      </li>
      <li>818 555 0192
        <svg viewBox="0 0 10 10" aria-hidden="true"><path d="M2.5 0 H7.5 V10 H2.5 Z M3.4 1.2 V7.8 H6.6 V1.2 Z M4.5 8.4 H5.5 V9.3 H4.5 Z"/></svg>
      </li>
      <li>info@ValmiraHealth.example
        <svg viewBox="0 0 10 10" aria-hidden="true"><path d="M0 2 H10 V8.5 H0 Z M0.6 2.4 L5 5.8 L9.4 2.4 Z" fill-rule="evenodd"/></svg>
      </li>
      <li>t.wrenfeld@ValmiraHealth.example
        <svg viewBox="0 0 10 10" aria-hidden="true"><circle cx="5" cy="5" r="4.8"/></svg>
      </li>
      <li>4100 East Marrow Drive Austin, TX 78119</li>
    </ul>
  </section>

  <section class="card card--brand" aria-label="Card front: brand">
    <p class="wordmark">VALMIRA</p>
    <p class="tagline">Integrative Holistic Medicine</p>
  </section>
</main>
</body>
</html>
```